Velvet Lantern rebranding my business with a new business card

I have my new logo and now I need a refresher on my business cards. I really want something fun and fresh. I like black background or anything to make the color pop.
Logo
Name: Velvet Lantern
Contact Info as stated below:
Mira Pellow
555-013-4762
Logo
Name: Velvet Lantern
Mira Pellow
555-013-4762
fb.me/VelvetLanternbyMira
Instagram: @VelvetLanternbyMira

Industry/Entity Type

Business

Contact Information for Business Card

double-sided. Logo on one side. Contact info on the other.

Requirements
Must have
• Logo
• Name: Velvet Lantern
• Contact Info as stated below:
• Mira Pellow
• 555-013-4762
• fb.me/VelvetLanternbyMira
• fb.me/VelvetLanternbyMira

```html
<!DOCTYPE html>
<html lang="en">
<head>
<meta charset="utf-8">
<title>Velvet Lantern – Business Card</title>
<link rel="stylesheet" href="https://fonts.googleapis.com/css2?family=Montserrat:wght@400;500&display=swap">
<style>
  :root {
    --backdrop: #d9d9d9;
    --kraft: #d5cba9;
    --paper: #ffffff;
    --teal: #2fb59b;
    --gold: #cbbd8e;
    --ink: #3a3a3a;
    --brand: #7a4a5e;
  }
  * { box-sizing: border-box; margin: 0; padding: 0; }
  html, body { width: 1200px; height: 800px; overflow: hidden; }
  body {
    background: var(--backdrop);
    font-family: "Montserrat", Arial, sans-serif;
    position: relative;
  }
  .card {
    position: absolute;
    top: 252px;
    width: 520px;
    height: 297px;
    box-shadow: 0 3px 10px rgba(0,0,0,0.15);
    overflow: hidden;
  }
  .card--front { left: 60px; background: var(--kraft); display: flex; align-items: center; justify-content: center; }
  .card--back { left: 620px; background: var(--paper); }

  .brand-mark {
    display: flex; align-items: center; gap: 12px;
    font-size: 30px; font-weight: 500; color: var(--brand);
    letter-spacing: 1px;
  }
  .brand-mark__dot { width: 22px; height: 22px; border-radius: 50%; background: var(--brand); }

  .badge {
    position: absolute; left: 78px; top: 88px;
    width: 120px; height: 120px; border-radius: 50%;
    border: 2px solid #e9c7d2;
    display: flex; align-items: center; justify-content: center; text-align: center;
    font-size: 15px; font-weight: 500; color: var(--brand); line-height: 1.2;
  }
  .divider { position: absolute; left: 236px; width: 3px; }
  .divider--gold { top: 92px; height: 26px; background: var(--gold); }
  .divider--teal { top: 132px; height: 62px; width: 2px; background: var(--teal); }

  .contact { position: absolute; left: 256px; top: 80px; }
  .contact__name { font-size: 20px; font-weight: 500; color: var(--teal); letter-spacing: 1.5px; text-transform: uppercase; }
  .contact__role { font-size: 12px; color: var(--ink); margin-top: 2px; }
  .contact__list { list-style: none; margin-top: 14px; }
  .contact__item { display: flex; align-items: center; gap: 10px; font-size: 13px; color: var(--ink); height: 20px; }
  .contact__item svg { width: 11px; height: 11px; flex: none; }

  .swoosh { position: absolute; inset: 0; }
</style>
</head>
<body>
  <section class="card card--front" aria-label="Card front">
    <div class="brand-mark"><span class="brand-mark__dot"></span>Velvet Lantern</div>
  </section>

  <section class="card card--back" aria-label="Card back">
    <svg class="swoosh" viewBox="0 0 520 297" aria-hidden="true">
      <path d="M300 297 C 380 250, 450 180, 520 118 L520 132 C 455 190, 390 255, 320 297 Z" fill="var(--teal)"/>
    </svg>
    <div class="badge">Velvet<br>Lantern</div>
    <span class="divider divider--gold"></span>
    <span class="divider divider--teal"></span>
    <div class="contact">
      <p class="contact__name">Mira Pellow</p>
      <p class="contact__role">Owner</p>
      <ul class="contact__list">
        <li class="contact__item">
          <svg viewBox="0 0 11 11"><rect x="2.5" y="0.5" width="6" height="10" rx="1" fill="none" stroke="var(--teal)"/></svg>
          555-013-4762
        </li>
        <li class="contact__item">
          <svg viewBox="0 0 11 11"><rect x="0.5" y="2" width="10" height="7" fill="var(--teal)"/><path d="M0.5 2 L5.5 6 L10.5 2" fill="none" stroke="#fff"/></svg>
          info@mirapellow.com
        </li>
        <li class="contact__item">
          <svg viewBox="0 0 11 11"><rect x="0.5" y="0.5" width="10" height="10" fill="var(--teal)"/></svg>
          me/VelvetLanternbyMira
        </li>
      </ul>
    </div>
  </section>
</body>
</html>
```